Product Page Images & A+ Content Design for TCG Storage Products

Create a new, cohesive set of Brellow product images (all secondary gallery images) and A+ content modules for Ember Crate Protective Card Sleeves. The goal is to clearly communicate protection, fit, clarity, and archival safety while looking more premium and distinctive than competing sleeve brands.

Primary benefits to communicate:
- Shield your cards from wear – blocks dust and resists surface scratches.
- The perfect fit for your collection – designed to fit all standard trading cards.
- Ultra‑clear smooth finish.
- Archival‑safe high‑quality materials – acid‑free, no PVC, non‑toxic, long‑term storage.

Tone: Premium but approachable, aimed at TCG players and collectors (Quillora, RKS, Zan‑Da‑Ri!, sports cards, etc.). Colour/theme be in keeping with the packaging design. Dark, with a pop of orange. Perhaps subtle textures or patterns, with a mythic/fantasy feel.

Existing product content is attached for reference.

Target Market(s)

Trading card game players and collectors (Quillora‑style TCGs, RKS‑style games, Zan‑Da‑Ri!‑style games, sports cards). Age: Mainly 14–40, skewed to hobbyist young adults. They care about condition and long‑term value of their cards, enjoy customising and protecting decks, responsive to “premium but good value” messaging.

Industry/Entity Type

Trading card accessories / tabletop gaming accessories. Protective sleeves and storage for trading card games and sports cards.

Font styles to use
Sans Serif

Requirements
Must have
• Clear communication of the four key benefits listed in the Project Description. Consistent use of Ember Crate logo and brand colours. Text that is readable on mobile thumbnails. Clean, uncluttered layouts that look professional next to leading competitors.
Nice to have
• Subtle fantasy / “mythic” visual touches that support the brand name (background textures, icons, gentle glow effects). Simple line‑art icons for key benefits (dust, scratch, fit, clarity, archival safe). Visual references to different card types (TCG, sports, etc.) using generic, non‑IP artwork. Light environmental storytelling (desk, playmat, storage box, binder). Lifestyle shots showing people playing or organising their collections.
Should not have
• Any copyrighted or licensed character artwork or logos. Over‑busy backgrounds or textures that distract from the product. Very long text blocks or small copy that is hard to read on mobile. Edgy, aggressive, or dark imagery that clashes with a family‑friendly hobby product. Inconsistent typography or colour schemes across images.

```html
<!DOCTYPE html>
<html lang="en">
<head>
<meta charset="utf-8">
<title>Ember Crate Protective Card Sleeves – Gallery Set</title>
<link rel="stylesheet" href="https://fonts.googleapis.com/css2?family=Poppins:wght@400;600&family=Roboto+Slab:wght@900&display=swap">
<style>
  :root{
    --board:#b3b3b3;
    --ink:#0b0b0b;
    --night:#121212;
    --paper:#ffffff;
    --paper-soft:#f1f2f4;
    --ember:#ff4a0a;
    --brand:#c9c2b4;
    --card-deep:#131b2e;
    --card-mid:#2d4f7e;
    --card-light:#8fb4d8;
    --card-edge:#e9e6df;
  }
  *{box-sizing:border-box;margin:0;padding:0}
  html,body{width:720px;height:1200px;overflow:hidden}
  body{background:radial-gradient(circle at 50% 30%,#c4c4c4,var(--board) 70%);font-family:"Poppins",sans-serif;position:relative}
  .panel{position:absolute;width:283px;height:283px;overflow:hidden;box-shadow:0 10px 24px rgba(0,0,0,.35)}
  .panel .bg{position:absolute;inset:0;width:100%;height:100%}
  .p1{left:54px;top:92px}.p2{left:383px;top:92px}
  .p3{left:54px;top:459px}.p4{left:383px;top:459px}
  .p5{left:54px;top:825px}.p6{left:383px;top:825px}
  .brand{position:absolute;display:flex;align-items:center;gap:6px;font-family:"Poppins",sans-serif;font-weight:600;color:var(--brand);font-size:11px;line-height:1.05;letter-spacing:.5px;text-transform:uppercase}
  .brand .mark{width:26px;height:26px;border-radius:50%;background:#2a2a2a;border:1px solid #444;flex:none}
  .headline{position:absolute;font-family:"Roboto Slab",serif;font-weight:900;line-height:.98;text-transform:uppercase;color:var(--ink)}
  .headline .hot{color:var(--ember);display:block}
  .headline .cold{display:block}
  .on-dark .headline{color:var(--paper)}
  .body-copy{position:absolute;font-size:11.5px;line-height:1.15;color:#1d1d1d}
  .card{position:absolute;border:3px solid var(--card-edge);background:linear-gradient(160deg,var(--card-deep),var(--card-mid) 45%,var(--card-light) 60%,var(--card-deep));box-shadow:0 3px 8px rgba(0,0,0,.4)}
  .card-frame{position:absolute;border:1px solid #f4a07c;background:var(--paper)}
  .feature{position:absolute;display:flex;align-items:center;gap:6px;font-size:9.5px;line-height:1.15;color:#1d1d1d}
  .icon{width:22px;height:22px;border-radius:50%;flex:none;display:flex;align-items:center;justify-content:center}
  .icon.dark{background:var(--ink)}
  .icon.hot{background:var(--ember)}
  .icon svg{width:12px;height:12px}
  .rail{position:absolute;left:13px;width:36px;text-align:center;color:var(--paper);font-size:7.5px}
  .rail .ring{width:17px;height:17px;margin:0 auto 3px;border-radius:50%;border:1.5px solid var(--ember);display:flex;align-items:center;justify-content:center}
  .rail .ring span{width:7px;height:7px;background:var(--paper);border-radius:2px}
  .stack-note{position:absolute;text-align:center;font-size:8.3px;line-height:1.2;color:#1d1d1d}
  .stack-note .icon{margin:0 auto 4px}
  .badge{position:absolute;text-align:center;color:var(--paper);font-size:9px;line-height:1.05}
  .badge .icon{margin:0 auto 2px;border:1.5px solid var(--paper)}
</style>
</head>
<body>

<!-- Panel 1: hero on dark -->
<section class="panel p1 on-dark">
  <svg class="bg" viewBox="0 0 283 283" aria-hidden="true">
    <defs><linearGradient id="dk1" x1="0" y1="0" x2="1" y2="1"><stop offset="0" stop-color="#050505"/><stop offset=".6" stop-color="#1a1a1a"/><stop offset="1" stop-color="#090909"/></linearGradient></defs>
    <rect width="283" height="283" fill="url(#dk1)"/>
    <rect y="277" width="283" height="6" fill="#fff"/>
    <g fill="var(--ember)"><polygon points="2,283 8,277 18,277 12,283"/><polygon points="22,283 28,277 38,277 32,283"/><polygon points="42,283 48,277 58,277 52,283"/><polygon points="132,283 138,277 148,277 142,283"/><polygon points="152,283 158,277 168,277 162,283"/><polygon points="172,283 178,277 188,277 182,283"/><polygon points="192,283 198,277 208,277 202,283"/></g>
  </svg>
  <div class="brand" style="left:22px;top:28px"><span class="mark"></span>Ember<br>Crate</div>
  <h2 class="headline" style="left:127px;top:22px;font-size:19px"><span class="cold">Protective</span><span class="hot">Card<br>Sleeves</span></h2>
  <div class="rail" style="top:107px"><div class="ring"><span></span></div>Protection</div>
  <div class="rail" style="top:139px"><div class="ring"><span></span></div>Fit</div>
  <div class="rail" style="top:171px"><div class="ring"><span></span></div>Clarity</div>
  <div class="rail" style="top:205px"><div class="ring"><span></span></div>Safety</div>
  <div class="card" role="img" aria-label="Sleeved trading card with fantasy creature artwork" style="left:57px;top:112px;width:60px;height:113px"></div>
  <div class="card" role="img" aria-label="Sleeved trading card with fantasy creature artwork" style="left:197px;top:112px;width:60px;height:113px"></div>
  <div class="card" role="img" aria-label="Sleeved trading card with fantasy creature artwork, front" style="left:113px;top:90px;width:88px;height:137px"></div>
</section>

<!-- Panel 2: product stack on dark -->
<section class="panel p2 on-dark">
  <svg class="bg" viewBox="0 0 283 283" aria-hidden="true">
    <defs><radialGradient id="dk2" cx=".5" cy=".35" r=".75"><stop offset="0" stop-color="#2a2a2a"/><stop offset="1" stop-color="#060606"/></radialGradient></defs>
    <rect width="283" height="283" fill="url(#dk2)"/>
  </svg>
  <div class="brand" style="left:88px;top:22px;font-size:13px"><span class="mark" style="width:34px;height:34px"></span>Ember<br>Crate</div>
  <div class="card" role="img" aria-label="Sleeved trading card with fantasy creature artwork" style="left:25px;top:105px;width:72px;height:133px"></div>
  <div class="card" role="img" aria-label="Sleeved trading card with fantasy creature artwork" style="left:187px;top:105px;width:72px;height:133px"></div>
  <div class="card" role="img" aria-label="Sleeved trading card with fantasy creature artwork, front" style="left:90px;top:78px;width:103px;height:160px"></div>
</section>

<!-- Panel 3: shield from wear -->
<section class="panel p3">
  <svg class="bg" viewBox="0 0 283 283" aria-hidden="true">
    <rect width="283" height="283" fill="var(--paper-soft)"/>
    <polygon points="0,0 283,0 283,20 145,20 115,62 0,62" fill="var(--ink)"/>
    <g><polygon points="150,28 158,20 178,20 170,28" fill="var(--ember)"/><polygon points="174,28 182,20 202,20 194,28" fill="var(--ink)"/><polygon points="198,28 206,20 226,20 218,28" fill="var(--ember)"/><polygon points="222,28 230,20 283,20 283,28" fill="var(--ink)"/></g>
  </svg>
  <div class="brand" style="left:22px;top:14px"><span class="mark"></span>Ember<br>Crate</div>
  <h2 class="headline" style="left:25px;top:85px;font-size:16.5px"><span class="hot">Shield<br>your cards</span><span class="cold">from wear</span></h2>
  <p class="body-copy" style="left:24px;top:143px;width:110px">Blocks dust and resists surface scratches</p>
  <div class="feature" style="left:26px;top:199px"><span class="icon dark"><svg viewBox="0 0 12 12"><circle cx="6" cy="6" r="3" fill="none" stroke="#fff" stroke-width="1.2"/></svg></span>Dust<br>Protection</div>
  <div class="feature" style="left:26px;top:231px"><span class="icon hot"><svg viewBox="0 0 12 12"><path d="M2 9 L9 2 M4 10 L10 4" stroke="#fff" stroke-width="1.3"/></svg></span>Scratch<br>Resistant</div>
  <div class="card-frame" style="left:144px;top:78px;width:118px;height:168px"></div>
  <div class="card" role="img" aria-label="Sleeved trading card with fantasy creature artwork" style="left:154px;top:87px;width:97px;height:150px"></div>
</section>

<!-- Panel 4: perfect fit -->
<section class="panel p4">
  <svg class="bg" viewBox="0 0 283 283" aria-hidden="true">
    <rect width="283" height="283" fill="var(--paper-soft)"/>
    <polygon points="0,0 283,0 283,20 145,20 115,62 0,62" fill="var(--ink)"/>
    <g><polygon points="150,28 158,20 178,20 170,28" fill="var(--ember)"/><polygon points="174,28 182,20 202,20 194,28" fill="var(--ink)"/><polygon points="198,28 206,20 226,20 218,28" fill="var(--ember)"/><polygon points="222,28 230,20 283,20 283,28" fill="var(--ink)"/></g>
    <g><polygon points="0,244 75,244 82,255 0,255" fill="var(--ink)"/><polygon points="75,244 100,244 107,255 82,255" fill="var(--ember)"/><polygon points="100,244 125,244 132,255 107,255" fill="var(--ink)"/><polygon points="125,244 150,244 157,255 132,255" fill="var(--ember)"/></g>
  </svg>
  <div class="brand" style="left:22px;top:14px"><span class="mark"></span>Ember<br>Crate</div>
  <h2 class="headline" style="left:23px;top:84px;font-size:17.5px"><span class="hot">The perfect<br>fit for</span><span class="cold">your<br>collection</span></h2>
  <p class="body-copy" style="left:23px;top:172px;width:120px;font-size:13px">Designed to fit all standard trading cards</p>
  <div class="card-frame" style="left:152px;top:85px;width:106px;height:130px;transform:skewX(-3deg)"></div>
  <div class="card" role="img" aria-label="Sleeved trading card with fantasy creature artwork" style="left:163px;top:92px;width:85px;height:116px;transform:skewX(-3deg)"></div>
</section>

<!-- Panel 5: ultra clear smooth finish -->
<section class="panel p5">
  <svg class="bg" viewBox="0 0 283 283" aria-hidden="true">
    <rect width="283" height="283" fill="var(--paper-soft)"/>
    <polygon points="190,0 283,0 283,283 250,283 135,205 112,135" fill="var(--ink)"/>
    <rect y="274" width="283" height="5" fill="var(--ink)"/>
    <g fill="var(--ember)"><polygon points="8,279 12,274 28,274 24,279"/><polygon points="40,279 44,274 60,274 56,279"/><polygon points="150,279 154,274 170,274 166,279"/><polygon points="182,279 186,274 202,274 198,279"/><polygon points="214,279 218,274 234,274 230,279"/></g>
  </svg>
  <h2 class="headline" style="left:25px;top:26px;font-size:21.5px"><span class="cold">Ultra-<br>clear</span><span class="hot">Smooth<br>finish</span></h2>
  <div class="brand" style="left:176px;top:62px"><span class="mark"></span>Ember<br>Crate</div>
  <div class="stack-note" style="left:20px;top:125px;width:73px"><span class="icon dark"><svg viewBox="0 0 12 12"><circle cx="6" cy="6" r="3.2" fill="none" stroke="#fff" stroke-width="1.2"/><circle cx="6" cy="6" r="1" fill="#fff"/></svg></span>Enjoy crystal clear visibility for vibrant artwork &amp; sharp details</div>
  <div class="stack-note" style="left:20px;top:206px;width:73px"><span class="icon hot"><svg viewBox="0 0 12 12"><path d="M3 9 Q6 3 9 3" stroke="#fff" stroke-width="1.4" fill="none"/></svg></span>Silky smooth feel that makes shuffling easy</div>
  <div class="card" role="img" aria-label="Sleeved trading card with fantasy creature artwork" style="left:94px;top:120px;width:55px;height:93px"></div>
  <div class="card" role="img" aria-label="Sleeved trading card with fantasy creature artwork" style="left:210px;top:120px;width:55px;height:93px"></div>
  <div class="card" role="img" aria-label="Sleeved trading card with fantasy creature artwork, front" style="left:140px;top:102px;width:75px;height:113px"></div>
</section>

<!-- Panel 6: archival safe -->
<section class="panel p6">
  <svg class="bg" viewBox="0 0 283 283" aria-hidden="true">
    <rect width="283" height="283" fill="var(--paper-soft)"/>
    <polygon points="0,0 283,0 283,20 145,20 115,62 0,62" fill="var(--ink)"/>
    <g><polygon points="150,28 158,20 178,20 170,28" fill="var(--ember)"/><polygon points="174,28 182,20 202,20 194,28" fill="var(--ink)"/><polygon points="198,28 206,20 226,20 218,28" fill="var(--ember)"/><polygon points="222,28 230,20 283,20 283,28" fill="var(--ink)"/></g>
    <polygon points="0,223 115,223 145,265 283,265 283,283 0,283" fill="var(--ember)"/>
  </svg>
  <div class="brand" style="left:22px;top:14px"><span class="mark"></span>Ember<br>Crate</div>
  <h2 class="headline" style="left:22px;top:92px;font-size:17.5px"><span class="hot">Archival-<br>safe</span><span class="cold">High<br>quality<br>materials</span></h2>
  <div class="badge" style="left:30px;top:212px;width:32px"><span class="icon dark"><svg viewBox="0 0 12 12"><path d="M6 2 Q9 6 9 8 A3 3 0 0 1 3 8 Q3 6 6 2Z" fill="#fff"/></svg></span>Acid<br>Free</div>
  <div class="badge" style="left:72px;top:212px;width:42px"><span class="icon dark"><svg viewBox="0 0 12 12"><path d="M4 2 H8 M5 2 V5 L3 10 H9 L7 5 V2" fill="none" stroke="#fff" stroke-width="1.1"/></svg></span>Non<br>Toxic</div>
  <div class="card-frame" style="left:144px;top:70px;width:114px;height:166px"></div>
  <div class="card" role="img" aria-label="Sleeved trading card with fantasy creature artwork" style="left:154px;top:80px;width:94px;height:146px"></div>
</section>

</body>
</html>
```